Brightway Haus Inc. Business Card Design

Brightway Haus Inc. is in search of a great clean design for our business cards!

Looking to incorporate our full logo and watermark on side one (however, I am open to having the text and watermark separated within the design.)

On side two, I am looking to have contact information (Name, Position, Phone #, Email, Website (www.thebrightwayhaus.ca). Can have the logo and/or watermark as part of the design if applicable.

Please add tagline "Where Shine Counts" on either side 1 or 2. This tagline can be in a sans serif, serif or cursive font as long as it compliments overall design. Capitalization can be title or sentence case depending on how it fits within the design.

Get creative!! Looking for a clean, crisp, premium design! Looking for a glossy card finish with spot UV features when printed. Cards will also be printed with rounded corners. Standard dimensions (3.5 x 2).

Target Market(s)

B2B - primary clients are business owners or property management corporations. (residential jobs are few and far between)

Industry/Entity Type

Business

Contact Information for Business Card

- clean, crisp design
- double sided
- spot UV accents and glossy finish upon printing
- standard business card size (3.5 x 2) with rounded corners
- please see project description for requirements per side

Font styles to use
Sans Serif

Requirements
Must have
• - adequate bleeds with print ready files
• - cohesive design elements between side 1 & 2
• - spot UV elements (can be on both sides or just one, use your discretion)
• - colour pallet should match the logo file provided
• - incorporate tagline "where shine counts" (this tagline can be in a serif or sans serif font as long as it is complimentary to the overall design.
Nice to have
• - Premium elements with a clean design
Should not have
• - Please omit cartoon or whimsical like designs, think premium.
• - Colours should not stray from the pallet of the provided logo.

```html
<!DOCTYPE html>
<html lang="en">
<head>
<meta charset="utf-8">
<title>Brightway Haus Inc. Business Cards</title>
<link rel="stylesheet" href="https://fonts.googleapis.com/css2?family=Montserrat:wght@500;600;800&family=Roboto:wght@400;500&display=swap">
<style>
  :root {
    --navy: #1d2660;
    --teal: #14b8bc;
    --white: #ffffff;
    --paper: #f7f8f9;
    --grey: #8a8d94;
    --backdrop: #e9eaec;
  }
  * { box-sizing: border-box; margin: 0; padding: 0; }
  html, body { width: 1200px; height: 911px; overflow: hidden; }
  body {
    background: var(--backdrop);
    font-family: "Roboto", sans-serif;
    position: relative;
  }
  .card {
    position: absolute;
    top: 123px;
    width: 380px;
    height: 665px;
    border-radius: 30px;
    overflow: hidden;
    background: var(--paper);
    box-shadow: 0 10px 30px rgba(20, 25, 60, 0.18);
  }
  .card--contact { left: 170px; }
  .card--brand { left: 650px; }

  .card__shape { position: absolute; inset: 0; width: 100%; height: 100%; }

  .brand-name {
    display: flex;
    align-items: center;
    gap: 10px;
    font-family: "Montserrat", sans-serif;
    font-weight: 800;
    color: var(--navy);
    letter-spacing: -0.5px;
    white-space: nowrap;
  }
  .brand-name__square {
    width: 20px; height: 20px;
    background: var(--teal);
    flex: none;
  }

  .card--contact .brand-name {
    position: absolute;
    top: 52px; left: 0; right: 0;
    justify-content: center;
    font-size: 25px;
  }
  .person {
    position: absolute;
    top: 158px; left: 0; right: 0;
    text-align: center;
    font-family: "Montserrat", sans-serif;
  }
  .person__name { color: var(--teal); font-weight: 600; font-size: 21px; letter-spacing: 0.5px; }
  .person__role { color: var(--navy); font-weight: 600; font-size: 14px; margin-top: 6px; letter-spacing: 0.4px; }

  .contact-list {
    position: absolute;
    top: 355px; left: 0; right: 0;
    list-style: none;
    text-align: center;
    color: var(--white);
    font-size: 16px;
    line-height: 1.2;
  }
  .contact-list li { margin-bottom: 10px; }
  .contact-list svg { display: block; margin: 0 auto 3px; width: 13px; height: 13px; fill: var(--teal); }

  .card--brand .brand-name {
    position: absolute;
    top: 70px; left: 0; right: 0;
    justify-content: center;
    font-size: 29px;
  }
  .tagline {
    position: absolute;
    top: 118px; left: 0; right: 0;
    text-align: center;
    font-family: "Roboto", sans-serif;
    font-size: 15px;
    letter-spacing: 6px;
    color: var(--grey);
  }
  .watermark-area {
    position: absolute;
    left: 0; right: 0; bottom: 0;
    height: 360px;
    background: linear-gradient(135deg, var(--navy) 0%, var(--navy) 45%, var(--teal) 100%);
  }
</style>
</head>
<body>

<section class="card card--contact" aria-label="Business card, contact side">
  <svg class="card__shape" viewBox="0 0 380 665" preserveAspectRatio="none" aria-hidden="true">
    <path fill="var(--navy)" d="M0,200 C30,300 180,330 380,300 L380,665 L0,665 Z"/>
    <path fill="var(--teal)" d="M0,200 C30,300 180,330 380,300 C200,345 20,330 0,250 Z"/>
    <path fill="var(--teal)" d="M80,160 C110,140 160,130 220,132 C150,140 110,155 90,178 Z"/>
  </svg>

  <div class="brand-name"><span class="brand-name__square"></span>Brightway Haus Inc.</div>

  <div class="person">
    <p class="person__name">MARCUS HALE</p>
    <p class="person__role">CEO/FOUNDER</p>
  </div>

  <ul class="contact-list">
    <li><svg viewBox="0 0 24 24"><path d="M6.6 10.8a15 15 0 0 0 6.6 6.6l2.2-2.2a1 1 0 0 1 1-.25 11.4 11.4 0 0 0 3.6.57 1 1 0 0 1 1 1V20a1 1 0 0 1-1 1A17 17 0 0 1 3 4a1 1 0 0 1 1-1h3.5a1 1 0 0 1 1 1c0 1.25.2 2.45.57 3.57a1 1 0 0 1-.25 1z"/></svg>604 555 0182</li>
    <li><svg viewBox="0 0 24 24"><path d="M7 1h10a2 2 0 0 1 2 2v18a2 2 0 0 1-2 2H7a2 2 0 0 1-2-2V3a2 2 0 0 1 2-2zm0 3v14h10V4z"/></svg>604 555 0247</li>
    <li><svg viewBox="0 0 24 24"><path d="M6 3h12v5H6zM3 9h18a1 1 0 0 1 1 1v7h-4v4H6v-4H2v-7a1 1 0 0 1 1-1zm5 7v3h8v-3z"/></svg>604 555 0391</li>
    <li><svg viewBox="0 0 24 24"><path d="M2 5h20v14H2zm2 2v.5l8 5 8-5V7z"/></svg>marcus@brightwayhaus.ca</li>
    <li><svg viewBox="0 0 24 24"><path d="M12 2a7 7 0 0 1 7 7c0 5-7 13-7 13S5 14 5 9a7 7 0 0 1 7-7zm0 4.5A2.5 2.5 0 1 0 12 11.5 2.5 2.5 0 0 0 12 6.5z"/></svg>1420 Harbour Crest Road<br>Halifax, Nova Scotia B3H 2Y9</li>
  </ul>
</section>

<section class="card card--brand" aria-label="Business card, brand side">
  <div class="brand-name"><span class="brand-name__square"></span>Brightway Haus Inc.</div>
  <p class="tagline">Where Shine Counts</p>
  <div class="watermark-area" role="img" aria-label="Large brand watermark in navy, teal and grey"></div>
</section>

</body>
</html>
```